Awesome Digital Ad Design – Vexora Adloop

I am going to be setting up a Vexora Adloop ad campaign I need creatives for.

Several sizes are needed in the end, however, please submit your design concept in the following 2 sizes to start:
Medium rectangle: 300X250
Leaderboard: 728X90

Original artwork/design files and images used expected upon payment and as part of the final delivery.

Ads should match our company brand and the information on this webpage: http://www.harbelstandwork.com/real-estate-marketing/
SEE MORE INSTRUCTIONS IN ATTACHED WORD DOC

Target Market(s)

Business-To-Business Audience –Real Estate Company Executives (Presidents/VPs/Owners/CEOs/Sales Managers).

Industry/Entity Type

Real Estate

Font styles to use
Sans Serif

Requirements
Must have
• Copy should be minimal words, billboard like. Please use real photos/images that would appeal to real estate high-level decision-maker executives.
Should not have
• No cartoons or graphics

```html
<!DOCTYPE html>
<html lang="en">
<head>
<meta charset="utf-8">
<title>Harbel Standwork – Vexora Adloop Ads</title>
<link href="https://fonts.googleapis.com/css2?family=Oswald:wght@500;600&family=Roboto+Condensed:wght@400;700&display=swap" rel="stylesheet">
<style>
  :root {
    --stage: #2d2d2d;
    --maroon: #72283a;
    --steel: #4e7692;
    --orange: #ef6b22;
    --orange-dark: #d65514;
    --gold: #c9b27a;
    --white: #ffffff;
    --ink: #222222;
  }
  * { margin: 0; padding: 0; box-sizing: border-box; }
  html, body { width: 1200px; height: 1200px; overflow: hidden; background: var(--stage); }
  body { position: relative; font-family: "Oswald", "Roboto Condensed", sans-serif; }

  /* Medium rectangle */
  .ad-rectangle {
    position: absolute; left: 208px; top: 98px; width: 787px; height: 655px; overflow: hidden;
  }
  .ad-rectangle .photo {
    position: absolute; inset: 0;
    background:
      linear-gradient(90deg, rgba(255,255,255,0) 55%, rgba(92,70,82,0.9) 70%, #5a4452 100%),
      linear-gradient(180deg, #dfe4ea 0%, #c9d3dc 45%, #a7bf8a 72%, #d9dcd6 100%);
  }
  .ad-rectangle .brand-box {
    position: absolute; left: 36px; top: 0; width: 162px; height: 157px;
    background: var(--white); display: flex; align-items: center; justify-content: center;
    gap: 8px;
  }
  .brand-name {
    font-family: "Roboto Condensed", sans-serif; font-weight: 400; color: var(--ink);
    font-size: 19px; line-height: 1.1;
  }
  .brand-dot { width: 12px; height: 12px; border-radius: 50%; background: var(--maroon); flex: none; }
  .band { position: absolute; left: 0; color: var(--white); padding-left: 36px; text-transform: uppercase; }
  .band-headline { top: 201px; width: 482px; height: 138px; background: var(--maroon); padding-top: 17px; }
  .band-offer { top: 354px; width: 406px; height: 118px; background: var(--steel); padding-top: 10px; }
  .band .line-sm { display: block; font-weight: 500; font-size: 47px; line-height: 52px; transform: scaleX(0.86); transform-origin: left; white-space: nowrap; }
  .band .line-lg { display: block; font-weight: 600; font-size: 62px; line-height: 64px; transform: scaleX(0.86); transform-origin: left; white-space: nowrap; }
  .band-offer .line-sm { font-size: 42px; line-height: 46px; }
  .band-offer .line-lg { font-size: 54px; line-height: 56px; }
  .cta {
    position: absolute; display: flex; align-items: center; justify-content: space-between;
    background: linear-gradient(180deg, #f47a2c, var(--orange-dark));
    border: 2px solid #f59a5c; color: var(--white); text-transform: uppercase;
  }
  .ad-rectangle .cta {
    left: 64px; top: 552px; width: 654px; height: 80px; border-radius: 10px; padding: 0 16px;
    font-size: 45px; font-weight: 500;
  }
  .cta .label { flex: 1; padding-left: 12px; transform: scaleX(0.86); transform-origin: left; white-space: nowrap; }

  /* Leaderboard */
  .ad-leaderboard {
    position: absolute; left: 53px; top: 915px; width: 1102px; height: 135px; overflow: hidden;
    background: var(--white);
  }
  .ad-leaderboard .photo {
    position: absolute; left: 0; top: 0; width: 230px; height: 135px;
    background: linear-gradient(90deg, #aab9c4 0%, #6b5560 45%, #59404c 70%, #8ea6b6 100%);
  }
  .ad-leaderboard svg.frame { position: absolute; inset: 0; }
  .lb-headline {
    position: absolute; left: 214px; top: 22px; font-family: "Roboto Condensed", sans-serif;
    font-weight: 700; text-transform: uppercase; line-height: 1;
  }
  .lb-headline .top { display: block; color: var(--white); font-size: 37px; }
  .lb-headline .bottom { display: block; color: var(--gold); font-size: 52px; margin-top: 2px; }
  .lb-offer {
    position: absolute; left: 611px; top: 22px; width: 280px; text-align: center;
    font-family: "Roboto Condensed", sans-serif; font-weight: 700; font-size: 27px; line-height: 26px;
    text-transform: uppercase;
  }
  .lb-offer .top { display: block; color: var(--white); }
  .lb-offer .bottom { display: block; color: var(--gold); }
  .ad-leaderboard .cta {
    left: 675px; top: 90px; width: 177px; height: 32px; border-radius: 3px; padding: 0 7px;
    font-size: 20px; font-weight: 500;
  }
  .ad-leaderboard .cta .label { padding-left: 6px; }
  .ad-leaderboard .brand-area {
    position: absolute; left: 950px; top: 0; width: 152px; height: 135px;
    display: flex; align-items: center; justify-content: center; gap: 7px;
  }
  .ad-leaderboard .brand-name { font-size: 17px; }
</style>
</head>
<body>

<section class="ad-rectangle" aria-label="Medium rectangle ad">
  <div class="photo" role="img" aria-label="Photo of a smiling real estate agent in a suit holding a sold sign in front of a house"></div>
  <div class="brand-box">
    <span class="brand-dot"></span>
    <span class="brand-name">Harbel<br>Standwork</span>
  </div>
  <div class="band band-headline">
    <span class="line-sm">Client Follow-Up</span>
    <span class="line-lg">Made Simple</span>
  </div>
  <div class="band band-offer">
    <span class="line-sm">Virtually No Cost To</span>
    <span class="line-lg">Your Company!</span>
  </div>
  <a class="cta">
    <svg width="46" height="46" viewBox="0 0 24 24" aria-hidden="true"><path fill="#fff" d="M6.6 10.8a15.2 15.2 0 0 0 6.6 6.6l2.2-2.2c.3-.3.7-.4 1-.2 1.1.4 2.3.6 3.6.6.6 0 1 .4 1 1V20c0 .6-.4 1-1 1A17 17 0 0 1 3 4c0-.6.4-1 1-1h3.5c.6 0 1 .4 1 1 0 1.3.2 2.5.6 3.6.1.3 0 .7-.2 1z"/><path fill="none" stroke="#fff" stroke-width="1.6" stroke-linecap="round" d="M14 6.5a4 4 0 0 1 3.5 3.5M14 3a7.5 7.5 0 0 1 7 7"/></svg>
    <span class="label">Call to Action: Learn More</span>
    <svg width="54" height="54" viewBox="0 0 24 24" aria-hidden="true"><circle cx="12" cy="12" r="11" fill="#f3f3f3"/><path fill="var(--orange)" d="M6 10h6V6l6 6-6 6v-4H6z"/></svg>
  </a>
</section>

<section class="ad-leaderboard" aria-label="Leaderboard ad">
  <div class="photo" role="img" aria-label="Photo of a smiling real estate agent holding a sold sign outside a house"></div>
  <svg class="frame" width="1102" height="135" viewBox="0 0 1102 135" aria-hidden="true">
    <defs>
      <linearGradient id="divider" x1="0" y1="0" x2="0" y2="1">
        <stop offset="0" stop-color="#7d9bb8"/><stop offset="0.5" stop-color="#ffffff"/><stop offset="1" stop-color="#c9b27a"/>
      </linearGradient>
    </defs>
    <polygon points="200,0 960,0 930,0 970,67 930,135 200,135 160,67" fill="var(--gold)"/>
    <polygon points="206,0 914,0 954,67 914,135 206,135 166,67" fill="var(--maroon)" transform="translate(8 0)"/>
    <polygon points="600,0 605,0 578,135 573,135" fill="url(#divider)"/>
  </svg>
  <div class="lb-headline">
    <span class="top">Client Follow-Up</span>
    <span class="bottom">Made Simple</span>
  </div>
  <div class="lb-offer">
    <span class="top">Virtually No Cost To</span>
    <span class="bottom">Your Company!</span>
  </div>
  <a class="cta">
    <svg width="20" height="20" viewBox="0 0 24 24" aria-hidden="true"><path fill="#fff" d="M6.6 10.8a15.2 15.2 0 0 0 6.6 6.6l2.2-2.2c.3-.3.7-.4 1-.2 1.1.4 2.3.6 3.6.6.6 0 1 .4 1 1V20c0 .6-.4 1-1 1A17 17 0 0 1 3 4c0-.6.4-1 1-1h3.5c.6 0 1 .4 1 1 0 1.3.2 2.5.6 3.6.1.3 0 .7-.2 1z"/></svg>
    <span class="label">Call to Action</span>
    <svg width="22" height="22" viewBox="0 0 24 24" aria-hidden="true"><circle cx="12" cy="12" r="11" fill="#f3f3f3"/><path fill="var(--orange)" d="M6 10h6V6l6 6-6 6v-4H6z"/></svg>
  </a>
  <div class="brand-area">
    <span class="brand-dot"></span>
    <span class="brand-name">Harbel<br>Standwork</span>
  </div>
</section>

</body>
</html>
```